Wordpress Design for a Digital Management Consulting Business

I need a simple Wordpress Design and someone to set it up for a new boutique management consulting business called Quillon Advisory that specialises in providing strategic advice to help grow digital businesses. It covers business strategy, marketing strategy, digital strategy, web product development, marketing campaigns, social, search, etc. From strategy to implementation.

URL is: quillonadvisory.com.au

My professional background is here: au.linkedin.com/in/hollyprenwick

Competitors: other boutique digital/marketing management consulting businesses in Australia

The logos, colours and fonts are attached.

I would like the site to convey a business that is Smart/intelligent, Contemporary, Progressive, Digital, Energetic, Friendly.

The objective of the site is to educate visitors about what Quillon Advisory does and encourage them to contact me for more information. It will be very light on content.

Target Market(s)

CEOs/Managing Directors, General Managers, Marketing Directors

Industry/Entity Type

Management Consulting

Font styles to use
Sans Serif

Colors
e34197
5c5c5c
000000

Requirements
Must have
• Site design requirements:
• Choose an appropriate Wordpress template, set it up for me and let me be able to edit it ongoing.
• It should use lots of images - these can be inspirational and not necessarily tied directly to the work
• Pink should feature, but not be the dominant colour.
• Site structure should be:
• 1. Home page - image led with horizontal navigation. Text beneath and images to describe the services.
• 2. About page - with space to write text and insert a picture of the Director
• 3. Services - with space to highlight services either as a list or graphically with text
• 4. Contact page - with space to write text and add email links, etc.
• Should have horizontal navigation
• It should have the flexibility to add another page
Nice to have
• Use the tree icon somehow in the design - consider in the background enlarged
• Use pink, grey, black from logo. Can introduce another complimentary colour if necessary.
• Can introduce another complimentary font to go with the logo font.
Should not have
• Use cliched business images and icons, eg. business suits, hand shakes, business men, business ties.

```html
<!DOCTYPE html>
<html lang="en">
<head>
<meta charset="utf-8">
<title>Quillon Advisory</title>
<link href="https://fonts.googleapis.com/css2?family=Questrial&family=Open+Sans:wght@400;600&display=swap" rel="stylesheet">
<style>
:root{
  --pink:#e34197;
  --grey:#5c5c5c;
  --black:#000000;
  --white:#ffffff;
}
*{box-sizing:border-box;margin:0;padding:0}
html,body{width:745px;height:1200px;overflow:hidden;background:var(--white)}
body{font-family:"Open Sans",Arial,sans-serif;color:var(--grey);position:relative}
.page{position:relative;width:745px;height:1200px;overflow:hidden}

/* header */
.site-header{position:absolute;top:0;left:0;width:745px;height:75px}
.brand{position:absolute;left:38px;top:16px;display:flex;align-items:center;gap:10px}
.brand-dot{width:34px;height:34px;border-radius:50%;background:var(--pink)}
.brand-name{font-family:"Questrial",Arial,sans-serif;font-size:28px;color:var(--pink);letter-spacing:1px;line-height:1}
.brand-name small{display:block;font-size:17px;letter-spacing:3px;margin-top:6px}
.contact-strip{position:absolute;right:60px;top:16px;font-size:10px;color:var(--grey)}
.contact-strip div{display:flex;align-items:center;gap:8px;height:20px}
.contact-strip .who{color:var(--pink)}

/* nav */
.main-nav{position:absolute;top:78px;left:0;width:745px;height:22px;background:var(--pink);display:flex;padding-left:70px}
.main-nav a{font-family:"Questrial",Arial,sans-serif;color:var(--white);font-size:9px;text-decoration:none;line-height:22px;padding:0 13px;letter-spacing:.3px}
.main-nav a.current{background:var(--black)}

/* hero */
.hero{position:absolute;top:104px;left:0;width:745px;height:298px;background:linear-gradient(90deg,#d9dadb 0%,#bfc2c5 45%,#8a8e93 100%)}
.hero-panel{position:absolute;left:62px;top:80px;width:222px;height:104px;background:rgba(40,40,40,.55);padding:10px}
.hero-panel h1{font-family:"Questrial",Arial,sans-serif;font-weight:400;font-size:24px;color:var(--white);margin-bottom:8px}
.hero-panel p{font-size:9.5px;color:var(--white);line-height:1.35}
.btn{position:absolute;left:68px;top:290px;background:var(--pink);color:var(--white);font-size:9.5px;padding:5px 10px;font-weight:600}

/* section titles with rules either side */
.section-title{position:absolute;left:0;width:745px;display:flex;align-items:center;justify-content:center;gap:18px;font-family:"Questrial",Arial,sans-serif;font-weight:400;font-size:30px;letter-spacing:5px;line-height:1}
.section-title::before,.section-title::after{content:"";display:block;width:95px;height:1px;background:currentColor;opacity:.55}
.services-title{top:440px;color:var(--black)}

/* services */
.service{position:absolute;top:525px;width:190px;text-align:center}
.service-photo{width:128px;height:128px;border-radius:50%;margin:0 auto;border:6px solid var(--pink);background:linear-gradient(135deg,#eef0f2,#aab4c0)}
.service h3{font-family:"Questrial",Arial,sans-serif;font-weight:400;font-size:17px;color:var(--black);margin:20px 0 6px;line-height:1.15}
.service p{font-size:9.5px;line-height:1.35;padding:0 14px}

/* what we do */
.what-band{position:absolute;top:830px;left:0;width:745px;height:337px;background:linear-gradient(180deg,#555557,#3f3f41)}
.what-title{top:855px;color:var(--white)}
.card{position:absolute;top:945px;width:186px;height:190px;background:var(--white)}
.card-photo{height:98px;background:linear-gradient(135deg,#d6d8db,#8c939b)}
.card h3{font-family:"Questrial",Arial,sans-serif;font-weight:400;font-size:14px;color:var(--pink);padding:8px 8px 4px;line-height:1.15}
.card p{font-size:9px;line-height:1.35;padding:0 8px}

/* footer */
.site-footer{position:absolute;top:1167px;left:0;width:745px;height:33px;background:var(--pink);color:var(--white);font-size:9px;text-align:center;line-height:33px}
</style>
</head>
<body>
<div class="page">
  <header class="site-header">
    <div class="brand"><span class="brand-dot"></span><span class="brand-name">QUILLON<small>ADVISORY</small></span></div>
    <div class="contact-strip">
      <div>
        <svg width="12" height="12" viewBox="0 0 24 24"><path fill="#5c5c5c" d="M6.6 10.8a15 15 0 0 0 6.6 6.6l2.2-2.2c.3-.3.7-.4 1-.2 1.1.4 2.3.6 3.6.6.6 0 1 .4 1 1V20c0 .6-.4 1-1 1A17 17 0 0 1 3 4c0-.6.4-1 1-1h3.5c.6 0 1 .4 1 1 0 1.3.2 2.5.6 3.6.1.3 0 .7-.2 1z"/></svg>
        <span class="who">Holly Prenwick</span><span>0400 555 018</span>
      </div>
      <div>
        <svg width="12" height="12" viewBox="0 0 24 24"><rect x="2" y="5" width="20" height="14" fill="none" stroke="#5c5c5c" stroke-width="2"/><path d="M2 5l10 8 10-8" fill="none" stroke="#5c5c5c" stroke-width="2"/></svg>
        <span>holly@quillonadvisory.com.au</span>
      </div>
    </div>
  </header>

  <nav class="main-nav">
    <a class="current" href="#">HOME</a>
    <a href="#">SERVICES</a>
    <a href="#">WHAT WE DO</a>
    <a href="#">ABOUT</a>
    <a href="#">DIRECTOR HOLLY PRENWICK</a>
    <a href="#">CLIENTS</a>
    <a href="#">CONTACT</a>
  </nav>

  <section class="hero" role="img" aria-label="Photo of a consultant reviewing a tablet in a bright office">
    <div class="hero-panel">
      <h1>Quillon Advisory</h1>
      <p>is a boutique management consulting company advising digital businesses across business, product and marketing strategy.</p>
    </div>
  </section>
  <span class="btn">Read More ›</span>

  <h2 class="section-title services-title">SERVICES</h2>
  <div class="service" style="left:59px">
    <div class="service-photo" role="img" aria-label="Photo of hands working with a digital chart"></div>
    <h3>Digital Strategy</h3>
    <p>Lorem Ipsum has been the industry's standard dummy text ever since the 1500s, when an unknown printer</p>
  </div>
  <div class="service" style="left:277px">
    <div class="service-photo" role="img" aria-label="Photo of a presenter at a whiteboard"></div>
    <h3>Marketing<br>Strategy</h3>
    <p>Lorem Ipsum has been the industry's standard dummy text ever since the 1500s, when an unknown printer</p>
  </div>
  <div class="service" style="left:495px">
    <div class="service-photo" role="img" aria-label="Photo of a digital globe network"></div>
    <h3>Marketing<br>Transformation</h3>
    <p>Lorem Ipsum has been the industry's standard dummy text ever since the 1500s, when an unknown printer</p>
  </div>

  <section class="what-band"></section>
  <h2 class="section-title what-title">WHAT WE DO</h2>
  <article class="card" style="left:67px">
    <div class="card-photo" role="img" aria-label="Photo of a team meeting around a table"></div>
    <h3>Strategic Thinking</h3>
    <p>Lorem Ipsum has been the industry's standard dummy text ever since the 1500s, when an unknown printer</p>
  </article>
  <article class="card" style="left:280px">
    <div class="card-photo" role="img" aria-label="Photo of analytics charts on a desk"></div>
    <h3>Analytical Approach</h3>
    <p>Lorem Ipsum has been the industry's standard dummy text ever since the 1500s, when an unknown printer</p>
  </article>
  <article class="card" style="left:493px">
    <div class="card-photo" role="img" aria-label="Photo of colleagues collaborating at a laptop"></div>
    <h3>End to end project Management</h3>
    <p>Lorem Ipsum has been the industry's standard dummy text ever since the 1500s, when an unknown printer</p>
  </article>

  <footer class="site-footer">© 2015 Copyright Quillon Advisory. All Rights Reserved</footer>
</div>
</body>
</html>
```